Federal Government Proposal Development Consulting company needs a website designed and coded

I am looking for someone to design (using an existing logo, color palette, and text fonts) and code a wordpress-based website for a Proposal Development consulting company. I have full copy for all site pages and suggestions for images/ graphics and a few example design templates to go from.

One note, from a color perspective - I included a mockup of a business card to highlight a color scheme that I tend to like - if you look at the back of the business card, the blend of the grey, blue, with the neon green highlight as a separator really seems to pop. Just a thought as you are designing the page.

I would like to see 2-3 potential design layouts, and I will select one to move forward with. Then, I would like the site to be coded for WordPress (I can provide a login to my wordpress site). I would like 1 opportunity to review the coded site and make any final tweaks.

```html
<!DOCTYPE html>
<html lang="en">
<head>
<meta charset="utf-8">
<title>Quillmark Proposals Consulting LLC</title>
<link href="https://fonts.googleapis.com/css2?family=Montserrat:wght@600;700;800&family=Didact+Gothic&family=Della+Respira&display=swap" rel="stylesheet">
<style>
:root{
  --blue:#0a5aa0;
  --blue-dark:#073f78;
  --navy:#0d1f3c;
  --ink:#222;
  --muted:#555;
  --sky:#8dcdeb;
  --footer:#0e1020;
  --white:#fff;
}
*{margin:0;padding:0;box-sizing:border-box}
html,body{width:1200px;height:4739px;overflow:hidden}
body{position:relative;background:var(--white);font-family:"Didact Gothic",sans-serif;color:var(--ink)}
.abs{position:absolute}
.heading{font-family:"Montserrat",sans-serif;font-weight:800;color:var(--navy);text-align:center;letter-spacing:1px}
.serif{font-family:"Della Respira",serif}

/* header */
.site-header{left:0;top:0;width:1200px;height:98px;background:var(--white)}
.brand{left:112px;top:14px;text-align:center;font-family:"Della Respira",serif;color:#6b6b75;font-size:30px;line-height:1}
.brand small{display:block;font-size:12px;margin-top:4px}
.brand-dot{display:inline-block;width:10px;height:10px;border-radius:50%;background:var(--blue);margin-left:6px;vertical-align:middle}
.nav{top:44px;font-family:"Didact Gothic",sans-serif;font-size:13px;color:#222}

/* hero */
.hero{left:0;top:98px;width:1200px;height:700px;background:linear-gradient(100deg,#0c2446 0%,#1b3c66 45%,#3b5c82 75%,#22334d 100%)}
.hero-title{left:122px;top:270px;font-family:"Montserrat",sans-serif;font-weight:800;font-size:48px;color:var(--white);letter-spacing:2px}
.hero-sub{left:126px;top:364px;font-size:24px;line-height:40px;color:var(--white)}
.btn-primary{left:130px;top:476px;width:192px;height:50px;background:#1967b5;color:var(--white);font-size:19px;display:flex;align-items:center;justify-content:center;letter-spacing:.5px}
.hero-edge{left:0;top:600px}

/* ornament */
.quill{width:170px;height:40px}

.lead{left:200px;top:1000px;width:800px;text-align:center;font-size:13.5px;line-height:29px;color:#333}

/* service cards */
.card{top:1185px;width:290px;height:315px;background:var(--white);box-shadow:0 2px 12px rgba(0,0,0,.14);border-bottom:5px solid var(--blue)}
.card .badge{position:absolute;left:20px;top:-18px;width:70px;height:70px;border-radius:50%;background:var(--white);box-shadow:0 2px 8px rgba(0,0,0,.18);display:flex;align-items:center;justify-content:center}
.card h3{position:absolute;left:30px;top:100px;font-family:"Montserrat",sans-serif;font-weight:700;font-size:20px;color:#1a1a1a}
.card p{position:absolute;left:30px;top:140px;width:245px;font-size:13px;line-height:29px;color:#333}

/* who we are */
.who-photo{left:0;top:1763px;width:620px;height:364px;background:linear-gradient(135deg,#cfd8e3 0%,#a9b7c6 50%,#6c7f95 100%)}
.who-box{left:600px;top:1795px;width:600px;height:293px;background:var(--blue);padding:30px 48px;color:var(--white);font-size:13px;line-height:26px}
.who-box p+p{margin-top:10px}
.btn-outline{display:inline-block;margin-top:12px;background:var(--white);color:#222;font-size:19px;padding:6px 18px;border-radius:3px}

/* carousel */
.svc{width:124px;height:124px;border-radius:50%;background:var(--white);border:2px solid #e3e9f0;box-shadow:0 2px 8px rgba(0,0,0,.08);display:flex;align-items:center;justify-content:center}
.svc-label{width:180px;text-align:center;font-family:"Montserrat",sans-serif;font-weight:700;font-size:17px;line-height:21px;color:#111}
.arrow-btn{width:26px;height:26px;border-radius:50%;border:1.5px solid #333;display:flex;align-items:center;justify-content:center}

/* expertise */
.expertise{left:0;top:2706px;width:1200px;height:520px;background:linear-gradient(180deg,#0b5eaa 0%,#0a5aa0 60%,#0c5296 100%)}
.tile{top:2875px;width:219px;height:225px;border-radius:4px}
.tile-label{top:3130px;width:219px;text-align:center;font-family:"Montserrat",sans-serif;font-weight:700;font-size:17px;line-height:21px;color:#dff0ff}

/* testimonials */
.quote{top:3440px;width:255px;height:320px;background:var(--white);box-shadow:0 2px 12px rgba(0,0,0,.14);padding:30px 26px}
.quote.active{background:var(--sky);color:var(--white)}
.quote .stars{font-size:12px;letter-spacing:2px}
.quote h4{font-family:"Montserrat",sans-serif;font-weight:700;font-size:17px;line-height:29px;margin-top:10px}
.quote p{font-size:11px;line-height:24px;margin-top:14px}
.quote .who{display:flex;align-items:center;margin-top:22px}
.avatar{width:56px;height:56px;border-radius:50%;background:linear-gradient(135deg,#c9d3de,#8ea1b5);flex:none}
.quote .name{margin-left:16px;font-family:"Della Respira",serif;font-size:14px;line-height:26px}

/* contact */
.contact{left:0;top:3858px;width:1200px;height:467px;background:linear-gradient(135deg,#0c4e92 0%,#0a5aa0 45%,#0a3f7a 100%)}
.field{background:var(--white);height:45px;font-size:13px;color:#333;padding:14px 16px}
.btn-submit{left:132px;top:4245px;width:106px;height:36px;background:#1565b9;color:var(--white);font-size:19px;display:flex;align-items:center;justify-content:center}
.contact-line{left:755px;display:flex;align-items:center;gap:16px;font-family:"Montserrat",sans-serif;font-weight:700;font-size:21px;color:var(--white)}

/* footer */
.site-footer{left:0;top:4325px;width:1200px;height:414px;background:var(--footer);color:var(--white)}
.foot-brand{left:126px;top:4372px;font-family:"Della Respira",serif;font-size:30px;color:var(--white);line-height:1}
.foot-brand small{display:block;font-size:12px;margin-top:4px;padding-left:40px}
.foot-about{left:132px;top:4490px;width:320px;font-size:15.5px;line-height:20px}
.foot-h{font-family:"Montserrat",sans-serif;font-weight:700;font-size:15px}
.foot-links{left:570px;top:4482px;font-size:15.5px;line-height:31px}
.foot-contact{left:802px;display:flex;align-items:center;gap:14px;font-size:15.5px}
.foot-rule{left:118px;top:4658px;width:964px;height:1px;background:#555}
.copyright{left:0;top:4698px;width:1200px;text-align:center;font-size:13px}
</style>
</head>
<body>

<header class="abs site-header">
  <div class="abs brand">Quillmark<span class="brand-dot"></span><small>Proposals Consulting LLC</small></div>
  <nav>
    <span class="abs nav" style="left:578px">HOME</span>
    <span class="abs nav" style="left:655px">WORK WITH US</span>
    <span class="abs nav" style="left:790px">WORK FOR US</span>
    <span class="abs nav" style="left:915px">ABOUT US</span>
    <span class="abs nav" style="left:1017px">CONTACT</span>
  </nav>
</header>

<section class="abs hero" role="img" aria-label="Photo of a consultant wearing a headset working at a laptop in a dark office"></section>
<svg class="abs hero-edge" width="1200" height="200" viewBox="0 0 1200 200" aria-hidden="true">
  <path d="M0 30 C200 150 420 150 640 130 C860 110 1040 60 1200 10 L1200 200 L0 200 Z" fill="#fff"/>
</svg>
<h1 class="abs hero-title">GENERATE SUCCESS</h1>
<p class="abs hero-sub serif">Fuel Innovation in Proposal Excellence with The<br>Quillmark Proposals! Click here to explore our services</p>
<a class="abs btn-primary">GET STARTED</a>

<!-- What we do -->
<svg class="abs quill" style="left:520px;top:888px" viewBox="0 0 170 40" role="img" aria-label="Blue quill ornament">
  <path d="M5 28 Q80 5 165 30 Q110 18 5 28 Z" fill="#123a8a"/>
</svg>
<h2 class="abs heading" style="left:0;top:935px;width:1216px;font-size:29px">WHAT WE DO</h2>
<p class="abs lead">Quillmark Proposals, specializes in advancing an organization through a comprehensive suite of services designed to modernize the proposal development process. From innovative Capture Management strategies that pinpoint lucrative opportunities, meticulous Proposal Development services that transform concepts into effective narratives, and cutting-edge Generative</p>

<article class="abs card" style="left:122px">
  <div class="badge"><svg width="40" height="40" viewBox="0 0 40 40" fill="none" stroke="#0a5aa0" stroke-width="2"><rect x="8" y="6" width="24" height="10" rx="2"/><rect x="8" y="22" width="24" height="10" rx="2"/><circle cx="13" cy="11" r="1.5"/><circle cx="13" cy="27" r="1.5"/></svg></div>
  <h3>Capture Management</h3>
  <p>Elevate your business development strategy with our Capture Management services. From opportunity identification to strategic planning, our experts will</p>
</article>
<article class="abs card" style="left:455px">
  <div class="badge"><svg width="40" height="40" viewBox="0 0 40 40" fill="none" stroke="#0a5aa0" stroke-width="2"><path d="M10 5h15l6 6v24H10z"/><path d="M14 16h12M14 22h8M14 28h6"/><path d="M24 30l8-10"/></svg></div>
  <h3>Proposal Development</h3>
  <p>Transform your vision into winning proposals with our Proposal Development services. We specialize in persuasive narratives, clear technical solutions, and</p>
</article>
<article class="abs card" style="left:788px">
  <div class="badge"><svg width="40" height="40" viewBox="0 0 40 40" fill="none" stroke="#0a5aa0" stroke-width="2"><circle cx="20" cy="20" r="9"/><text x="20" y="24" font-size="9" text-anchor="middle" fill="#0a5aa0" stroke="none" font-family="Montserrat,sans-serif" font-weight="700">AI</text><path d="M20 3v6M20 31v6M3 20h6M31 20h6M8 8l4 4M28 28l4 4M32 8l-4 4M8 32l4-4"/></svg></div>
  <h3>Generative AI</h3>
  <p>Revolutionize your proposal writing process with our domain-aware Generative AI services. Using customer-installed tools, we leverage domain-aware artificial</p>
</article>

<!-- Who we are -->
<svg class="abs quill" style="left:522px;top:1620px" viewBox="0 0 170 40" role="img" aria-label="Blue quill ornament">
  <path d="M5 28 Q80 5 165 30 Q110 18 5 28 Z" fill="#123a8a"/>
</svg>
<h2 class="abs heading" style="left:0;top:1675px;width:1252px;font-size:29px">WHO WE ARE</h2>
<div class="abs who-photo" role="img" aria-label="Photo of a smiling presenter leading a meeting with colleagues around a table"></div>
<div class="abs who-box">
  <p>Lorem ipsum dolor sit amet, consectetur adipiscing elit, sed do eiusmod tempor incididunt ut labore et dolore magna aliqua. Ut enim ad minim veniam, quis nostrud exercitation ullamco laboris nisi ut aliquip ex ea commodo consequat. Duis aute irure dolor in reprehenderit in voluptate velit esse cillum dolore eu fugiat nulla</p>
  <p>Sed ut perspiciatis unde omnis iste natus error sit voluptatem accusantium doloremque laudantium, totam rem aperiam,.</p>
  <span class="btn-outline">READ MORE</span>
</div>

<!-- Our services -->
<svg class="abs quill" style="left:525px;top:2248px" viewBox="0 0 170 40" role="img" aria-label="Blue quill ornament">
  <path d="M5 28 Q80 5 165 30 Q110 18 5 28 Z" fill="#123a8a"/>
</svg>
<h2 class="abs heading" style="left:0;top:2296px;width:1256px;font-size:29px">OUR SERVICES</h2>
<svg class="abs" style="left:130px;top:2385px" width="940" height="190" viewBox="0 0 940 190" fill="none" stroke="#333" stroke-width="2" stroke-dasharray="2 4" aria-hidden="true">
  <path d="M11 95 A90 90 0 0 0 191 95"/>
  <path d="M191 95 A90 90 0 0 1 373 95"/>
  <path d="M373 95 A90 90 0 0 0 553 95"/>
  <path d="M553 95 A90 90 0 0 1 735 95"/>
  <path d="M735 95 A90 90 0 0 0 917 95"/>
  <g stroke="none"><circle cx="11" cy="95" r="6" fill="#0a5aa0"/><circle cx="191" cy="95" r="5" fill="#666"/><circle cx="373" cy="95" r="5" fill="#666"/><circle cx="553" cy="95" r="5" fill="#666"/><circle cx="735" cy="95" r="5" fill="#666"/><circle cx="917" cy="95" r="6" fill="#0a5aa0"/></g>
</svg>
<div class="abs arrow-btn" style="left:60px;top:2493px"><svg width="10" height="10" viewBox="0 0 10 10"><path d="M7 1L3 5l4 4" stroke="#333" stroke-width="1.5" fill="none"/></svg></div>
<div class="abs arrow-btn" style="left:1102px;top:2493px"><svg width="10" height="10" viewBox="0 0 10 10"><path d="M3 1l4 4-4 4" stroke="#333" stroke-width="1.5" fill="none"/></svg></div>

<div class="abs svc" style="left:169px;top:2418px"><svg width="56" height="56" viewBox="0 0 56 56" fill="none" stroke="#0a5aa0" stroke-width="2"><rect x="10" y="6" width="30" height="40" rx="2"/><circle cx="25" cy="22" r="7"/><circle cx="40" cy="40" r="9"/><path d="M40 35v10M37 38h5"/></svg></div>
<div class="abs svc" style="left:351px;top:2418px"><svg width="56" height="56" viewBox="0 0 56 56" fill="none" stroke="#0a5aa0" stroke-width="2"><circle cx="28" cy="28" r="12"/><text x="28" y="33" font-size="12" text-anchor="middle" fill="#0a5aa0" stroke="none" font-family="Montserrat,sans-serif" font-weight="700">AI</text><path d="M28 6v8M28 42v8M6 28h8M42 28h8M12 12l6 6M38 38l6 6M44 12l-6 6M12 44l6-6"/></svg></div>
<div class="abs svc" style="left:533px;top:2418px"><svg width="56" height="56" viewBox="0 0 56 56" fill="none" stroke="#0a5aa0" stroke-width="2"><circle cx="28" cy="32" r="10"/><circle cx="28" cy="32" r="4"/><path d="M28 18v-4M18 32h-6M44 32h-6M20 14a12 12 0 0 1 16 0M16 10a18 18 0 0 1 24 0"/></svg></div>
<div class="abs svc" style="left:721px;top:2418px"><svg width="56" height="56" viewBox="0 0 56 56" fill="none" stroke="#0a5aa0" stroke-width="2"><path d="M28 8l16 9v18l-16 9-16-9V17z"/><path d="M12 17l16 9 16-9M28 26v18"/><path d="M6 10v36M50 10v36"/></svg></div>
<div class="abs svc" style="left:891px;top:2418px"><svg width="56" height="56" viewBox="0 0 56 56" fill="none" stroke="#0a5aa0" stroke-width="2"><rect x="8" y="8" width="28" height="36" rx="2"/><path d="M14 16h16M14 22h12"/><path d="M30 46V34M36 46V28M42 46V36M48 46V30"/></svg></div>

<div class="abs svc-label" style="left:141px;top:2585px">Proposal<br>Management</div>
<div class="abs svc-label" style="left:323px;top:2585px">Generative AI</div>
<div class="abs svc-label" style="left:505px;top:2585px">Technical<br>Solutioning</div>
<div class="abs svc-label" style="left:693px;top:2585px">Volume Lead</div>
<div class="abs svc-label" style="left:863px;top:2583px">Capture<br>Management</div>

<!-- Expertise -->
<section class="abs expertise"></section>
<svg class="abs quill" style="left:530px;top:2738px" viewBox="0 0 170 40" role="img" aria-label="White quill ornament">
  <path d="M5 28 Q80 5 165 30 Q110 18 5 28 Z" fill="#e8f1fb"/>
</svg>
<h2 class="abs heading" style="left:0;top:2783px;width:1228px;font-size:29px;color:#fff">SUBJECT MATTER EXPERTISE</h2>
<div class="abs arrow-btn" style="left:40px;top:2993px;border-color:#cfe2f5"><svg width="10" height="10" viewBox="0 0 10 10"><path d="M7 1L3 5l4 4" stroke="#cfe2f5" stroke-width="1.5" fill="none"/></svg></div>
<div class="abs arrow-btn" style="left:1128px;top:2993px;border-color:#cfe2f5"><svg width="10" height="10" viewBox="0 0 10 10"><path d="M3 1l4 4-4 4" stroke="#cfe2f5" stroke-width="1.5" fill="none"/></svg></div>
<div class="abs tile" style="left:96px;background:linear-gradient(160deg,#0c1f3e 0%,#2a4f86 55%,#c08a3a 100%)" role="img" aria-label="Image of a glowing digital globe over circuit lines"></div>
<div class="abs tile" style="left:353px;background:linear-gradient(160deg,#3f5670 0%,#1f2d40 60%,#5a6f86 100%)" role="img" aria-label="Photo of an engineer working at multiple monitors"></div>
<div class="abs tile" style="left:617px;background:linear-gradient(160deg,#4a4f58 0%,#a8723e 55%,#3a3f48 100%)" role="img" aria-label="Photo of stacked cardboard boxes in a warehouse"></div>
<div class="abs tile" style="left:884px;background:linear-gradient(160deg,#06214f 0%,#0b4fb0 55%,#2aa0ff 100%)" role="img" aria-label="Image of a hand touching digital gear icons"></div>
<div class="abs tile-label" style="left:96px">Generative AI</div>
<div class="abs tile-label" style="left:353px">Systems<br>Engineering</div>
<div class="abs tile-label" style="left:617px">Logistics</div>
<div class="abs tile-label" style="left:884px">Systems Integration</div>

<!-- Testimonials -->
<svg class="abs quill" style="left:540px;top:3318px" viewBox="0 0 170 40" role="img" aria-label="Blue quill ornament">
  <path d="M5 28 Q80 5 165 30 Q110 18 5 28 Z" fill="#123a8a"/>
</svg>
<h2 class="abs heading" style="left:0;top:3350px;width:1250px;font-size:29px">TESTIMONIALS</h2>

<article class="abs quote" style="left:-72px">
  <div class="stars">★★★★★</div>
  <h4>Lorem ipsum dolor sit amet, consectetur</h4>
  <p style="font-size:13.5px;line-height:24px">sed do eiusmod tempor incididunt ut labore et dolore magna aliqua consectetur adipiscing</p>
  <div class="who"><span class="avatar" role="img" aria-label="Client portrait"></span><span class="name">Lena Voss<br>Client</span></div>
</article>
<article class="abs quote" style="left:228px">
  <div class="stars">★★★★★</div>
  <h4>Lorem ipsum dolor sit amet, consectetur</h4>
  <p>sed do eiusmod tempor incididunt ut labore et dolore magna aliqua</p>
  <div class="who"><span class="avatar" role="img" aria-label="Client portrait"></span><span class="name">Owen Pratt<br>Client</span></div>
</article>
<article class="abs quote active" style="left:512px">
  <div class="stars">★★★★★</div>
  <h4>Lorem ipsum dolor sit amet, consectetur</h4>
  <p>sed do eiusmod tempor incididunt ut labore et dolore magna aliqua consectetur adipiscing elit, sed</p>
  <div class="who"><span class="avatar" role="img" aria-label="Client portrait"></span><span class="name">Nina Coles<br>Client</span></div>
</article>
<article class="abs quote" style="left:815px">
  <div class="stars">★★★★★</div>
  <h4>Lorem ipsum dolor sit amet, consectetur</h4>
  <p>sed do eiusmod tempor incididunt ut labore et dolore magna aliqua consectetur adipiscing elit, sed</p>
  <div class="who"><span class="avatar" role="img" aria-label="Client portrait"></span><span class="name">Evan Dorsey<br>Client</span></div>
</article>
<article class="abs quote" style="left:1120px">
  <div class="stars">★★★★★</div>
  <h4>Lorem ipsum dolor sit amet,</h4>
  <p>sed do eiusmod ut labore</p>
  <div class="who"><span class="avatar" role="img" aria-label="Client portrait"></span></div>
</article>

<!-- Contact -->
<section class="abs contact" role="img" aria-label="Blue background with faint digital code texture"></section>
<h2 class="abs heading" style="left:0;top:3906px;width:1254px;font-size:29px;color:#fff">CONTACT US</h2>
<div class="abs field" style="left:132px;top:3982px;width:256px">First Name</div>
<div class="abs field" style="left:402px;top:3982px;width:256px">Las Name</div>
<div class="abs field" style="left:132px;top:4045px;width:256px">Phone</div>
<div class="abs field" style="left:402px;top:4045px;width:256px">Email</div>
<div class="abs field" style="left:132px;top:4108px;width:526px;height:92px">Message</div>
<a class="abs btn-submit">SUBMIT</a>
<div class="abs contact-line" style="top:4044px"><svg width="24" height="18" viewBox="0 0 24 18" fill="none" stroke="#fff" stroke-width="1.6"><rect x="1" y="1" width="22" height="16" rx="1"/><path d="M1 1l11 9 11-9"/></svg>hello@quillmarkproposals.com</div>
<div class="abs contact-line" style="top:4119px"><svg width="22" height="22" viewBox="0 0 24 24" fill="none" stroke="#fff" stroke-width="1.6"><path d="M5 2h4l2 5-3 2a12 12 0 0 0 7 7l2-3 5 2v4a2 2 0 0 1-2 2A18 18 0 0 1 3 4a2 2 0 0 1 2-2z"/></svg>(410) 555-0186</div>

<!-- Footer -->
<footer class="abs site-footer"></footer>
<div class="abs foot-brand">Quillmark<span class="brand-dot" style="background:#2d6fd1"></span><small>Proposals Consulting LLC</small></div>
<p class="abs foot-about">Quillmark Proposals, specializes in advancing an organization through a comprehensive suite of services designed to modernize the proposal development process</p>
<div class="abs foot-h" style="left:568px;top:4436px;color:#fff">QUICK LINKS</div>
<ul class="abs foot-links" style="list-style:none;color:#fff">
  <li>Home</li><li>Work with Us</li><li>Work for Us</li><li>About Us</li><li>Contact</li>
</ul>
<div class="abs foot-h" style="left:796px;top:4440px;color:#fff">CONTACT US</div>
<div class="abs foot-contact" style="top:4490px;color:#fff"><svg width="22" height="16" viewBox="0 0 24 18" fill="none" stroke="#fff" stroke-width="1.6"><rect x="1" y="1" width="22" height="16" rx="1"/><path d="M1 1l11 9 11-9"/></svg>hello@quillmarkproposals.com</div>
<div class="abs foot-contact" style="top:4535px;color:#fff"><svg width="20" height="20" viewBox="0 0 24 24" fill="none" stroke="#fff" stroke-width="1.6"><path d="M5 2h4l2 5-3 2a12 12 0 0 0 7 7l2-3 5 2v4a2 2 0 0 1-2 2A18 18 0 0 1 3 4a2 2 0 0 1 2-2z"/></svg>(410) 555-0186</div>
<div class="abs foot-rule"></div>
<p class="abs copyright" style="color:#fff">© Copyrights QUILLMARK PROPOSALS CONSULTING LLC.All rights reserved</p>

</body>
</html>
```